Kestrel Facilities Business Card Design

We would now like to design business cards with the new Kestrel Facilities logo

Target Market(s)

Professional

Industry/Entity Type

Professional services

Contact Information for Business Card

Employee name, title, phone number, email address, corporate office address and logo.

Font styles to use
Sans Serif

Colors
0054AA
0677BA
7BADD7
CADEEF
E8F1F8

Requirements
Must have
• My logo
Should not have
• any other pictures or images besides my logo

```html
<!DOCTYPE html>
<html lang="en">
<head>
<meta charset="UTF-8">
<title>Kestrel Facilities Business Card</title>
<link href="https://fonts.googleapis.com/css2?family=Montserrat:wght@400;500;700;800&display=swap" rel="stylesheet">
<style>
  :root {
    --bg: #2a2a2c;
    --brand-blue: #3375bc;
    --brand-silver: #d3d8e4;
    --stripe-grey: #a6a6a6;
    --card-white: #ffffff;
    --ink: #1d1d1f;
  }
  * { margin: 0; padding: 0; box-sizing: border-box; }
  html, body {
    width: 1200px; height: 960px; overflow: hidden;
    background: var(--bg);
    font-family: "Montserrat", sans-serif;
  }
  .stage { position: relative; width: 1200px; height: 960px; }
  .card {
    position: absolute; left: 250px; width: 700px; height: 400px;
    border-radius: 22px; overflow: hidden;
    box-shadow: 0 14px 30px rgba(0,0,0,0.45);
  }
  .card-back {
    top: 50px; background: var(--brand-blue);
    display: flex; align-items: center; justify-content: center;
  }
  .card-front { top: 510px; background: var(--card-white); }
  .card-bands { position: absolute; inset: 0; }

  .brand-name {
    display: flex; align-items: center; gap: 18px;
    font-weight: 800; text-transform: uppercase; line-height: 1.05;
    letter-spacing: 2px;
  }
  .brand-name .brand-square { flex: none; width: 54px; height: 54px; }
  .card-back .brand-name { color: var(--brand-silver); font-size: 46px; }
  .card-back .brand-square { background: var(--brand-silver); width: 70px; height: 70px; }

  .card-front .brand-name {
    position: absolute; left: 60px; top: 165px;
    color: var(--brand-blue); font-size: 32px;
  }
  .card-front .brand-square { background: var(--brand-blue); }

  .divider {
    position: absolute; left: 372px; top: 125px;
    width: 2px; height: 175px; background: var(--brand-blue);
  }
  .contact {
    position: absolute; left: 398px; top: 115px;
    color: var(--ink); font-size: 15px; line-height: 1.35;
  }
  .contact .person-name {
    color: var(--brand-blue); font-weight: 800; font-size: 22px;
    letter-spacing: 0.5px;
  }
  .contact .person-title { font-size: 16px; margin-bottom: 14px; }
  .contact .address { margin-bottom: 14px; }
  .contact .channel { display: flex; align-items: center; gap: 8px; }
  .contact .channel svg { width: 14px; height: 14px; flex: none; fill: var(--brand-blue); }
</style>
</head>
<body>
<div class="stage">

  <section class="card card-back" aria-label="Card back">
    <div class="brand-name">
      <span class="brand-square"></span>
      <span>Kestrel<br>Facilities</span>
    </div>
  </section>

  <section class="card card-front" aria-label="Card front">
    <svg class="card-bands" viewBox="0 0 700 400" preserveAspectRatio="none" aria-hidden="true">
      <path d="M0 0H700V26H272L250 92H0Z" fill="var(--brand-blue)"/>
      <path d="M276 40H700V52H282L276 70H262Z" fill="var(--stripe-grey)"/>
      <path d="M0 374H440L462 308H700V400H0Z" fill="var(--brand-blue)"/>
      <path d="M0 348H418L424 330H438L430 360H0Z" fill="var(--stripe-grey)"/>
    </svg>

    <div class="brand-name">
      <span class="brand-square"></span>
      <span>Kestrel<br>Facilities</span>
    </div>

    <div class="divider"></div>

    <div class="contact">
      <div class="person-name">DANA WHITFIELD</div>
      <div class="person-title">Co-Founder</div>
      <div class="address">4812 N. Harbor Lane<br>Suite 1204 Ridgeport.14</div>
      <div class="channel">
        <svg viewBox="0 0 16 16"><path d="M3 1l3 3-2 2c1 2 3 4 5 5l2-2 3 3-2 3C7 15 1 9 0 4z"/></svg>
        <span>+254-555-01742</span>
      </div>
      <div class="channel">
        <svg viewBox="0 0 16 16"><path d="M0 3h16v10H0z M1 4l7 5 7-5" stroke="#fff" stroke-width="1"/></svg>
        <span>info@kestrelfacilities.com</span>
      </div>
      <div class="channel">
        <svg viewBox="0 0 16 16"><circle cx="8" cy="8" r="7"/><path d="M1 8h14M8 1c-3 4-3 10 0 14M8 1c3 4 3 10 0 14" stroke="#fff" stroke-width="1" fill="none"/></svg>
        <span>www.kestrelfacilities.com</span>
      </div>
    </div>
  </section>

</div>
</body>
</html>
```